Ridgeway Mining Solutions Business Card

Ridgeway Mining Solutions is a company that provides consulting services to the Mining Industry.

Whilst Ridgeway Mining Solutions is an Australian based company its client base is the global mining industry.

The essence of Ridgeway Mining Solutions is its a can do organisation that can make a difference to its clients by providing quality assistance and form lasting relationships.
Updates

Target Market(s)

The global Mining Industry.

Industry/Entity Type

Mining

Font styles to use
Serif

Colors

Designer to choose colors to be used in the design.

Requirements
Nice to have
• My thinking is the card would look good in black given the logo.

I would like to see written on the back side of the card " Providing Metallurgical, Management and Corporate Services to the Mining Industry"

```html
<!DOCTYPE html>
<html lang="en">
<head>
<meta charset="utf-8">
<title>Ridgeway Mining Solutions – Business Card</title>
<link rel="stylesheet" href="https://fonts.googleapis.com/css2?family=Lora:wght@400;700&display=swap">
<style>
  :root {
    --card-black: #000000;
    --accent-orange: #f7a21b;
    --text-white: #ffffff;
    --photo-dark: #3a2414;
    --photo-mid: #8a4f22;
    --photo-warm: #c8741f;
  }
  * { margin: 0; padding: 0; box-sizing: border-box; }
  html, body {
    width: 1200px;
    height: 741px;
    overflow: hidden;
    background: var(--card-black);
  }
  .card {
    position: relative;
    width: 1200px;
    height: 741px;
    background: var(--card-black);
    font-family: "Lora", Georgia, serif;
    color: var(--text-white);
    text-align: center;
    overflow: hidden;
  }
  .brand {
    position: absolute;
    top: 128px;
    left: 0;
    width: 100%;
    color: var(--accent-orange);
    font-weight: 700;
    line-height: 1;
  }
  .brand-name {
    display: block;
    font-size: 60px;
    letter-spacing: 2px;
  }
  .brand-sub {
    display: block;
    margin-top: 10px;
    font-size: 20px;
    letter-spacing: 3px;
  }
  .person-name {
    position: absolute;
    top: 288px;
    left: 0;
    width: 100%;
    font-size: 74px;
    font-weight: 400;
    color: var(--accent-orange);
    line-height: 1.1;
  }
  .person-role {
    position: absolute;
    top: 390px;
    left: 0;
    width: 100%;
    font-size: 29px;
    font-weight: 400;
  }
  .contact {
    position: absolute;
    top: 488px;
    left: 0;
    width: 100%;
    font-size: 26px;
    line-height: 37px;
  }
  .footer-band {
    position: absolute;
    left: 0;
    bottom: 0;
    width: 100%;
    height: 46px;
    background: var(--accent-orange);
  }
  .photo-strip {
    position: absolute;
    left: 335px;
    bottom: 0;
    width: 550px;
    height: 148px;
    background: linear-gradient(90deg, var(--photo-mid) 0%, var(--photo-dark) 35%, var(--photo-warm) 55%, var(--photo-dark) 80%, var(--photo-mid) 100%);
  }
</style>
</head>
<body>
  <div class="card">
    <div class="brand">
      <span class="brand-name">RIDGEWAY</span>
      <span class="brand-sub">MINING SOLUTIONS</span>
    </div>
    <h1 class="person-name">Name Here</h1>
    <p class="person-role">Position Here ex. Engineer</p>
    <p class="contact">
      48 Hay St Perth, WA 6000&nbsp; Australia<br>
      Phone : +61 8 5550 1427&nbsp; Email :&nbsp; info@ridgewaymining.com.au
    </p>
    <div class="footer-band"></div>
    <div class="photo-strip" role="img" aria-label="Photo strip of mining scenes: rock and ore close-up and large haul truck tyres"></div>
  </div>
</body>
</html>
```